Business Card for Beach theme sports bar called MORVIN

I need a business card designed for our employees, front and back. This will be used by the employees of two business locations to hand out to customers. I've attached the previous business cards we used at one time for a Dantells (it is now Morvin). Looking for a fresh new card that is elegant but has character.

Target Market(s)

30-60, middle class

Contact Information for Business Card

We are a beach bar and sports bar. I am looking for an elegant business card with the front to have the MORVIN logo. Then on the back I need it to allow a space for employees to write their names and for them to write in their schedule. I have attached our old cards with our old name Dantells so you can pull everything we need on the cards. one thing is missing is we have another location at 2615 W Calder Ridge Rd with a number of 702-418-9053. Since we will use it for both locations it should allow the employee to circle or check mark the bar which they work at.

Font styles to use
Sans Serif

Requirements
Must have
• We are looking for some fresh ideas for the business card. Something that will really stick out to customers when the staff hands them out. Creativity will be looked at positively, but we still want it to look upscale and fun.

```html
<!DOCTYPE html>
<html lang="en">
<head>
<meta charset="utf-8">
<title>Morvin – Business Card</title>
<link rel="stylesheet" href="https://fonts.googleapis.com/css2?family=Arimo:wght@400;700&family=Lato:wght@400&family=Tinos&display=swap">
<style>
  :root {
    --backdrop: #d6d6d6;
    --card: #242424;
    --card-dark: #1c1c1c;
    --card-light: #3a3a3a;
    --white: #ffffff;
    --red: #e0252b;
    --yellow: #fff200;
  }
  * { margin: 0; padding: 0; box-sizing: border-box; }
  html, body { width: 1200px; height: 1200px; overflow: hidden; }
  body {
    background: var(--backdrop);
    position: relative;
    font-family: "Lato", sans-serif;
    color: var(--white);
  }
  .card {
    position: absolute;
    left: 250px;
    width: 708px;
    height: 404px;
    background: var(--card);
    box-shadow: 0 6px 14px rgba(0,0,0,0.3);
    overflow: hidden;
  }
  .card--front { top: 144px; }
  .card--back { top: 582px; }

  .front-pattern {
    position: absolute; inset: 0;
    background: linear-gradient(100deg, var(--card-dark) 0%, var(--card) 45%, var(--card-light) 100%);
  }
  .front-brand {
    position: absolute; left: 0; right: 0; top: 160px;
    text-align: center;
    font-family: "Arimo", sans-serif;
    font-weight: 700;
    font-size: 88px;
    letter-spacing: 1px;
    color: var(--white);
  }
  .front-brand-mark {
    position: absolute; left: 50%; top: 96px;
    width: 38px; height: 38px; margin-left: -19px;
    border-radius: 50%;
    background: var(--red);
  }
  .front-tagline {
    position: absolute; left: 0; right: 0; top: 314px;
    text-align: center;
    font-family: "Tinos", serif;
    font-size: 32px;
    letter-spacing: 1px;
    color: var(--red);
  }

  .offer {
    position: absolute; left: 36px; top: 34px;
    font-family: "Arimo", sans-serif;
    font-weight: 700;
    font-size: 70px;
    letter-spacing: -0.5px;
    line-height: 1;
    color: var(--yellow);
    white-space: nowrap;
  }
  .schedule { position: absolute; left: 41px; top: 142px; width: 356px; }
  .schedule-days, .schedule-boxes { display: flex; }
  .schedule-day {
    width: 50.5px; text-align: center;
    font-family: "Arimo", sans-serif; font-weight: 700; font-size: 24px;
  }
  .schedule-boxes { margin-top: 6px; }
  .schedule-box {
    width: 50.5px; height: 42px;
    border: 2px solid var(--white);
    margin-right: -2px;
  }
  .staff-label {
    position: absolute; left: 74px; top: 226px; width: 280px;
    text-align: center;
    font-family: "Arimo", sans-serif; font-weight: 700; font-size: 38px;
    letter-spacing: 1px;
    color: var(--yellow);
  }
  .staff-name {
    position: absolute; left: 74px; top: 270px;
    width: 280px; height: 94px;
    border: 2px solid var(--white);
  }
  .back-brand {
    position: absolute; left: 470px; width: 192px; top: 122px;
    text-align: center;
    font-family: "Arimo", sans-serif; font-weight: 700; font-size: 54px;
    color: var(--white);
  }
  .back-brand-mark {
    position: absolute; left: 554px; top: 108px;
    width: 22px; height: 22px; border-radius: 50%;
    background: var(--red);
  }
  .locations {
    position: absolute; left: 440px; width: 250px; top: 236px;
    text-align: center; font-size: 16px; line-height: 20px;
  }
  .location + .location { margin-top: 13px; }
  .fine-print {
    position: absolute; left: 0; right: 0; top: 370px;
    text-align: center; font-size: 10.5px;
  }
</style>
</head>
<body>
  <section class="card card--front">
    <div class="front-pattern" role="img" aria-label="Faint repeating palm-leaf pattern on dark background"></div>
    <div class="front-brand-mark"></div>
    <div class="front-brand">Morvin</div>
    <div class="front-tagline">A Gamers Bar</div>
  </section>

  <section class="card card--back">
    <h1 class="offer">$20 MATCH PLAY</h1>
    <div class="schedule">
      <div class="schedule-days">
        <span class="schedule-day">M</span><span class="schedule-day">T</span><span class="schedule-day">W</span><span class="schedule-day">Th</span><span class="schedule-day">F</span><span class="schedule-day">Sa</span><span class="schedule-day">Su</span>
      </div>
      <div class="schedule-boxes">
        <span class="schedule-box"></span><span class="schedule-box"></span><span class="schedule-box"></span><span class="schedule-box"></span><span class="schedule-box"></span><span class="schedule-box"></span><span class="schedule-box"></span>
      </div>
    </div>
    <div class="staff-label">Bartender</div>
    <div class="staff-name"></div>

    <div class="back-brand-mark"></div>
    <div class="back-brand">Morvin</div>
    <address class="locations" style="font-style:normal">
      <p class="location">2615 W Calder Ridge Rd<br>702-418-9053</p>
      <p class="location">3380 W Harlow Basin Rd<br>Las Vegas, NV 89146<br>702-551-6284<br>cs@morvinbar.com</p>
    </address>
    <p class="fine-print">Match play for new slot members, must play total 100 coin.&nbsp; Please see bartender for details.&nbsp; Management reserves all rights</p>
  </section>
</body>
</html>
```